Chimney Service company needs new business card design

We need a updated business card with our new logo added. We provide a full range of chimney services throughout Vermont and New Hampshire. The business card will be one sided and color. Attached is our current business card another document showing all the information we would like on the card.
We dont like a lot of flashy colors.... here is a link to our website to get an idea of our branding www.flueguardianvt.example

Target Market(s)

homeowners

Industry/Entity Type

Business

Contact Information for Business Card

See attached sheet for content.

Font styles to use
Serif
Sans Serif

Requirements
Must have
• all information provided on separate sheet
Should not have
• Additional information that may clogg up design

```html
<!DOCTYPE html>
<html lang="en">
<head>
<meta charset="utf-8">
<title>Flue Guardian – Business Card</title>
<link href="https://fonts.googleapis.com/css2?family=Oswald:wght@500&family=Roboto:wght@400&display=swap" rel="stylesheet">
<style>
  :root {
    --backdrop: #2a2a2a;
    --card: #f2f2f2;
    --charcoal: #333333;
    --charcoal-dark: #2b2b2b;
    --brand-red: #a30c0c;
    --ink: #3a3a3a;
    --on-dark: #ffffff;
  }
  * { box-sizing: border-box; margin: 0; padding: 0; }
  html, body { width: 1200px; height: 871px; overflow: hidden; }
  body { background: var(--backdrop); position: relative; }

  .business-card {
    position: absolute; left: 75px; top: 135px;
    width: 1050px; height: 600px;
    background: var(--card);
    overflow: hidden;
  }

  .card-header {
    position: absolute; left: 56px; top: 56px; height: 84px;
    display: flex; align-items: center; gap: 22px;
  }
  .brand-square { width: 84px; height: 84px; background: var(--charcoal); flex: none; }
  .brand-name {
    font-family: "Roboto", sans-serif; font-weight: 400; font-size: 44px;
    color: var(--ink); line-height: 1;
  }

  .service-band {
    position: absolute; left: 0; top: 194px; width: 611px; height: 335px;
    background: var(--charcoal); padding: 24px 56px;
    color: var(--on-dark);
  }
  .headline {
    font-family: "Oswald", sans-serif; font-weight: 500; font-size: 28px;
    line-height: 33px; text-transform: uppercase;
  }
  .service-list { list-style: none; margin-top: 14px; }
  .service-list li {
    font-family: "Roboto", sans-serif; font-size: 25px; line-height: 31px;
    padding-left: 32px; position: relative;
  }
  .service-list li::before {
    content: ""; position: absolute; left: 4px; top: 12px;
    width: 8px; height: 8px; border-radius: 50%; background: var(--on-dark);
  }

  .mark-panel { position: absolute; left: 617px; top: 194px; width: 329px; height: 335px; background: var(--charcoal-dark); }
  .accent-strip { position: absolute; left: 954px; top: 194px; width: 96px; height: 335px; background: var(--brand-red); }

  .contact-row {
    position: absolute; left: 56px; top: 546px; height: 34px;
    display: flex; align-items: center; gap: 14px;
    font-family: "Roboto", sans-serif; font-size: 24px; color: var(--ink);
    white-space: nowrap;
  }
  .contact-item { display: flex; align-items: center; gap: 6px; }
  .contact-item svg { width: 20px; height: 20px; fill: var(--brand-red); flex: none; }
</style>
</head>
<body>
  <section class="business-card">
    <header class="card-header">
      <div class="brand-square"></div>
      <div class="brand-name">Flue Guardian</div>
    </header>

    <div class="service-band">
      <p class="headline">Serving VT &amp; New Hampshire since 1989<br>Fully insured — Free estimates<br>Family owned &amp; operated</p>
      <ul class="service-list">
        <li>Full Masonry Services</li>
        <li>Historic chimney restoration</li>
        <li>Stainless steel liners</li>
        <li>New Chimney installations</li>
        <li>FSCA Certified Chimney sweeps</li>
      </ul>
    </div>
    <div class="mark-panel"></div>
    <div class="accent-strip"></div>

    <footer class="contact-row">
      <span class="contact-item">
        <svg viewBox="0 0 24 24"><path d="M6.6 10.8a15.5 15.5 0 0 0 6.6 6.6l2.2-2.2c.3-.3.7-.4 1-.2 1.1.4 2.3.6 3.6.6.6 0 1 .4 1 1V20c0 .6-.4 1-1 1A17 17 0 0 1 3 4c0-.6.4-1 1-1h3.5c.6 0 1 .4 1 1 0 1.3.2 2.5.6 3.6.1.3 0 .7-.2 1z"/></svg>
        802-555-0147
      </span>
      <span class="contact-item">
        <svg viewBox="0 0 24 24"><path d="M2 5h20v14H2z"/><path d="M3 6l9 7 9-7" fill="none" stroke="#f2f2f2" stroke-width="1.6"/></svg>
        info@flueguardianvt.example
      </span>
      <span class="contact-item">
        <svg viewBox="0 0 24 24"><circle cx="12" cy="12" r="10"/><path d="M2 12h20M12 2c3 3 3 17 0 20M12 2c-3 3-3 17 0 20" fill="none" stroke="#f2f2f2" stroke-width="1.4"/></svg>
        www.flueguardianvt.example
      </span>
    </footer>
  </section>
</body>
</html>
```